Provide bookkeeping and accounting services to small and growing businesses

We need website and logo design using the name Dornaby as the logo.
The target audience are small companies and startups who need:
1) Simple bookkeeping services
2) Accounting advice that only someone with many years of senior financial experience as a CPA can provide.

The services are provided by two individuals. each of whom specialize in one of the areas.

We want the website to be clean without a lot of visual distraction but don't know how to make a boring subject interesting. We believe our potential clients, small business owners, need to find what they want quickly and easily without a lot of verbiage or distractions.

We've attached a draft of the homepage and have completed the text on most of the other pages.

Target Market(s)

small and early stage growth companies in San Diego North County

Industry/Entity Type

Accounting

Number of Pages Required

1 page

Font styles to use
Sans Serif

Colors
86cfc6
33b8a4
85cae6

Requirements
Must have
• We need a design for the website homepage that includes the name Dornaby as the logo. Must include a design for the name.
• Must have color in teal or greenish blue.
Nice to have
• White background, clean, clear, uncluttered.
• We would like to use the design in a Theme on a WordPress website. Themes Paper Lantern and Quiet Harbour are appealing to us.
Should not have
• Moving pictures

```html
<!DOCTYPE html>
<html lang="en">
<head>
<meta charset="utf-8">
<title>Dornaby Accounting and Bookkeeping</title>
<link href="https://fonts.googleapis.com/css2?family=Cinzel:wght@400;500&family=Lato:wght@400;700&family=Cabin:wght@600&display=swap" rel="stylesheet">
<style>
:root{
  --teal:#33b8a4;
  --teal-soft:#86cfc6;
  --sky:#85cae6;
  --ink:#1e1e1e;
  --text:#2b2b2b;
  --rule:#cfe7e3;
  --footer:#474747;
  --footer-text:#f2f2f2;
  --field:#c9c9c9;
}
*{margin:0;padding:0;box-sizing:border-box}
html,body{width:886px;height:1200px;overflow:hidden;background:#fff}
body{position:relative;font-family:"Lato",sans-serif;color:var(--text)}
.abs{position:absolute}

/* header */
.site-header{position:absolute;left:0;top:0;width:886px;height:106px;background:linear-gradient(#e6f6f4,#fff 60px);border-bottom:2px solid #222}
.header-phone{position:absolute;right:42px;top:8px;font:700 14px "Lato",sans-serif;color:var(--ink);display:flex;align-items:center;gap:5px}
.brand{position:absolute;left:0;width:886px;top:18px;text-align:center;font:400 25px "Cinzel",serif;color:var(--teal)}
.main-nav{position:absolute;top:76px;left:0;width:886px;display:flex;justify-content:center;font:400 12px "Cinzel",serif;letter-spacing:.5px;color:var(--ink)}
.main-nav span{padding:0 15px;border-left:1px solid #bbb;line-height:14px}
.main-nav span:first-child{border-left:none}
.nav-active-bar{position:absolute;left:173px;top:94px;width:53px;height:12px;background:linear-gradient(#fff,var(--teal-soft))}

/* hero */
.hero-band{position:absolute;left:0;top:106px;width:886px;height:376px;background:linear-gradient(#e8e8e8,#dcdcdc)}
.hero-photo{position:absolute;top:107px;height:346px}
.photo-a{left:0;width:287px;background:linear-gradient(135deg,#eef0f4,#aab4cc 60%,#4a5468)}
.photo-b{left:299px;width:287px;background:linear-gradient(160deg,#4f9fd6,#c89a7a 50%,#7fb8e0)}
.photo-c{left:599px;width:287px;background:linear-gradient(120deg,#f4f6f8,#c9ced4 55%,#8a939c)}
.hero-title{position:absolute;left:0;width:886px;top:360px;text-align:center;font:600 29px/36px "Cabin",sans-serif;color:#111;text-shadow:0 0 6px rgba(255,255,255,.7)}

/* services */
.services-panel{position:absolute;left:59px;top:453px;width:768px;height:260px;background:#fff}
.section-title{font:400 18px "Cinzel",serif;color:var(--ink);font-variant:small-caps}
.section-title em{font-style:normal;color:var(--teal)}
.rule{position:absolute;height:1px;background:var(--rule)}
.rule i{position:absolute;left:0;top:-1px;height:2px;background:var(--teal)}
.service-card{position:absolute;top:526px;width:151px}
.service-photo{width:151px;height:104px;box-shadow:0 3px 4px rgba(0,0,0,.2)}
.service-name{margin-top:18px;font:400 13px "Cinzel",serif;color:var(--ink);letter-spacing:.4px}
.service-text{margin-top:8px;font:400 10.5px/14.5px "Lato",sans-serif;color:var(--text);white-space:nowrap}
.service-text b{font-weight:400;color:var(--teal)}
.carousel-arrow{position:absolute;top:569px}

/* welcome */
.welcome-title{position:absolute;left:59px;top:748px;font:400 20px/25px "Cinzel",serif;color:var(--ink);font-variant:small-caps;letter-spacing:.5px}
.welcome-title em{font-style:normal;color:var(--teal)}
.welcome-photo{position:absolute;left:59px;top:833px;width:148px;height:129px;border:2px solid #777;background:linear-gradient(135deg,#dfe4e8,#aeb6be 60%,#e9ecef)}
.welcome-text{position:absolute;left:230px;top:829px;width:284px;font:400 10.8px/16.8px "Lato",sans-serif;letter-spacing:.35px;color:var(--text)}
.btn{position:absolute;width:63px;height:19px;background:var(--teal);color:#fff;font:700 11px/19px "Lato",sans-serif;text-align:center;border-radius:2px}

/* inquiry */
.divider{position:absolute;left:547px;top:752px;width:1px;height:200px;background:linear-gradient(transparent,#ddd 20%,#ddd 80%,transparent)}
.inquiry-title{position:absolute;left:574px;top:748px;display:flex;align-items:center;gap:14px;font:400 19px "Cinzel",serif;font-variant:small-caps;color:var(--ink)}
.inquiry-title em{font-style:normal;color:var(--teal)}
.field-label{position:absolute;left:575px;font:400 10.5px "Lato",sans-serif;color:var(--text)}
.field{position:absolute;left:627px;width:200px;height:19px;border:1px solid var(--field);background:#fff}

/* footer */
.site-footer{position:absolute;left:0;top:994px;width:886px;height:176px;background:linear-gradient(#3f3f3f,#555)}
.footer-title{position:absolute;top:1014px;font:400 14px "Cinzel",serif;font-variant:small-caps;color:var(--footer-text);letter-spacing:.5px}
.footer-rule{position:absolute;top:1044px;height:1px;background:#888}
.quick-links{position:absolute;left:60px;top:1056px;list-style:none;font:400 10.5px/14.6px "Lato",sans-serif;color:var(--footer-text)}
.quick-links li::before{content:"";display:inline-block;border-left:4px solid var(--teal);border-top:3px solid transparent;border-bottom:3px solid transparent;margin-right:8px;vertical-align:1px}
.quick-links li.current{color:var(--teal)}
.col-shade{position:absolute;top:1048px;width:2px;height:96px;background:linear-gradient(#3a3a3a,#333,#3a3a3a)}
.contact-block{position:absolute;left:304px;font:400 10.5px/13.5px "Lato",sans-serif;color:var(--footer-text)}
.contact-block strong{font-weight:700}
.social{position:absolute;top:1058px;width:26px;height:26px;border-radius:50%;border:2px solid #fff}
.footer-brand{position:absolute;left:654px;top:1102px;font:400 19px/20px "Cinzel",serif;color:#5f6262}
.copyright-bar{position:absolute;left:0;top:1170px;width:886px;height:30px;background:var(--teal);text-align:center;font:400 10.5px/30px "Lato",sans-serif;color:#1a1a1a}
</style>
</head>
<body>

<header class="site-header">
  <div class="header-phone">
    <svg width="11" height="14" viewBox="0 0 11 14"><path d="M2 1 L4.5 1 L5 4 L3.5 5 C4 7.5 5.5 9.5 7 10.5 L8.5 9 L10.5 10.5 L10 13 C5 13 1 8 1 2 Z" fill="#33b8a4"/></svg>
    012-555-0147
  </div>
  <div class="brand">Dornaby Accounting and Bookkeeping</div>
  <nav class="main-nav">
    <span>HOME</span><span>ABOUT US</span><span>SERVICES</span><span>EXPERIENCE</span><span>RESOURCES</span><span>CONTACT US</span>
  </nav>
</header>
<div class="nav-active-bar"></div>

<section class="hero">
  <div class="hero-band"></div>
  <div class="hero-photo photo-a" role="img" aria-label="Hand with pen reviewing financial charts beside a calculator"></div>
  <div class="hero-photo photo-b" role="img" aria-label="Business handshake over a blue data background"></div>
  <div class="hero-photo photo-c" role="img" aria-label="Two businessmen looking at a laptop"></div>
  <h1 class="hero-title">Dornaby Accounting and Bookkeeping services,<br>A leap forward a better future.</h1>
</section>

<section class="services">
  <div class="services-panel"></div>
  <h2 class="section-title abs" style="left:101px;top:468px">Our <em>Services</em></h2>
  <div class="rule" style="left:101px;top:504px;width:685px"><i style="width:125px"></i></div>

  <svg class="carousel-arrow" style="left:64px" width="10" height="18" viewBox="0 0 10 18"><path d="M8 2 L2 9 L8 16" fill="none" stroke="#33b8a4" stroke-width="1.5"/></svg>
  <svg class="carousel-arrow" style="left:808px" width="10" height="18" viewBox="0 0 10 18"><path d="M2 2 L8 9 L2 16" fill="none" stroke="#33b8a4" stroke-width="1.5"/></svg>

  <article class="service-card" style="left:98px">
    <div class="service-photo" role="img" aria-label="Hands using a calculator over a ledger" style="background:linear-gradient(135deg,#e8e8e8,#9a9a9a 55%,#3c3c3c)"></div>
    <h3 class="service-name">BOOKKEEPING</h3>
    <p class="service-text">Lorem ipsum dolor sit amet,<br>consectetuer adipiscing aed <b>[...]</b></p>
  </article>
  <article class="service-card" style="left:277px">
    <div class="service-photo" role="img" aria-label="Team reviewing colourful charts with a calculator" style="background:linear-gradient(135deg,#8fb4d8,#f2efe8 50%,#e0a24a)"></div>
    <h3 class="service-name">CONTROLLER SERVICES</h3>
    <p class="service-text">Lorem ipsum dolor sit amet,<br>consectetuer adipiscing elit <b>[...]</b></p>
  </article>
  <article class="service-card" style="left:455px">
    <div class="service-photo" role="img" aria-label="Business team meeting around a table" style="background:linear-gradient(135deg,#d9dde2,#5c6470 55%,#c8ccd2)"></div>
    <h3 class="service-name">CFO SERVICES</h3>
    <p class="service-text">Lorem ipsum dolor sit amet,<br>consectetuer adipiscing elitd <b>[...]</b></p>
  </article>
  <article class="service-card" style="left:634px">
    <div class="service-photo" role="img" aria-label="Payroll sheet with a pen" style="background:linear-gradient(135deg,#4a4a40,#e4e7ee 45%,#b8c0d4)"></div>
    <h3 class="service-name">PAYROLL</h3>
    <p class="service-text">Lorem ipsum dolor sit amet,<br>consectetuer adipiscing elit <b>&nbsp;[...]</b></p>
  </article>
</section>

<section class="welcome">
  <h2 class="welcome-title">Welcome To<br><em>Dornaby</em> Accounting and Bookkeeping</h2>
  <div class="rule" style="left:59px;top:812px;width:452px"><i style="width:108px"></i></div>
  <div class="welcome-photo" role="img" aria-label="Glass office door opening onto a bright office"></div>
  <p class="welcome-text">Dornaby offers a flexible range of accounting and bookkeeping services and support for small and growing organizations in San Diego North County. We provide bookkeeping services specializing in LedgerWise® at your offices or remotely from ours. We also provide a broad range of accounting services or financial advice.</p>
  <div class="btn" style="left:230px;top:944px">Read More</div>
</section>

<div class="divider"></div>

<section class="inquiry">
  <h2 class="inquiry-title">
    <svg width="20" height="14" viewBox="0 0 20 14"><rect x="0.5" y="0.5" width="19" height="13" fill="#86cfc6"/><path d="M0.5 0.5 L10 8 L19.5 0.5 M0.5 13.5 L7.5 6.5 M19.5 13.5 L12.5 6.5" fill="none" stroke="#fff" stroke-width="1.2"/></svg>
    <span>Quick <em>Inquiry</em></span>
  </h2>
  <div class="rule" style="left:574px;top:783px;width:253px"><i style="width:108px"></i></div>
  <span class="field-label" style="top:801px">Name:</span><div class="field" style="top:797px"></div>
  <span class="field-label" style="top:830px">Company:</span><div class="field" style="top:827px"></div>
  <span class="field-label" style="top:859px">Subject :</span><div class="field" style="top:856px"></div>
  <span class="field-label" style="top:899px">Message :</span><div class="field" style="top:889px;height:33px"></div>
  <div class="btn" style="left:627px;top:944px;font-size:12px">Submit</div>
</section>

<footer>
  <div class="site-footer"></div>
  <h3 class="footer-title" style="left:60px">Quick Links</h3>
  <div class="footer-rule" style="left:58px;width:102px"></div>
  <ul class="quick-links">
    <li class="current">Home</li><li>About Us</li><li>Services</li><li>Experience</li><li>Resources</li><li>Contact Us</li>
  </ul>
  <div class="col-shade" style="left:226px"></div>

  <h3 class="footer-title" style="left:304px">Contact Information</h3>
  <div class="footer-rule" style="left:304px;width:200px"></div>
  <svg class="abs" style="left:304px;top:1058px" width="8" height="11" viewBox="0 0 8 11"><path d="M4 11 L1 5 A3 3 0 1 1 7 5 Z" fill="#33b8a4"/><circle cx="4" cy="4" r="1.2" fill="#474747"/></svg>
  <div class="contact-block" style="left:323px;top:1056px"><strong>Dornaby Accounting and Bookkeeping</strong><br>48 Lanternview Court Suite 310, Carlsmere,<br>CA 92011</div>
  <svg class="abs" style="left:303px;top:1106px" width="10" height="11" viewBox="0 0 11 14"><path d="M2 1 L4.5 1 L5 4 L3.5 5 C4 7.5 5.5 9.5 7 10.5 L8.5 9 L10.5 10.5 L10 13 C5 13 1 8 1 2 Z" fill="#33b8a4"/></svg>
  <div class="contact-block" style="left:320px;top:1104px;font-weight:700;font-size:12px">012-555-0147</div>
  <svg class="abs" style="left:303px;top:1133px" width="10" height="7" viewBox="0 0 10 7"><rect width="10" height="7" fill="#33b8a4"/><path d="M0 0 L5 4 L10 0" fill="none" stroke="#474747" stroke-width=".8"/></svg>
  <div class="contact-block" style="left:321px;top:1129px">info@dornaby.com</div>
  <div class="col-shade" style="left:576px"></div>

  <h3 class="footer-title" style="left:654px;font-size:13px;top:1012px">Follow Us</h3>
  <div class="footer-rule" style="left:654px;width:171px"></div>
  <div class="social" style="left:654px;background:#3b5c9a" role="img" aria-label="Social profile"></div>
  <div class="social" style="left:689px;background:#3aa8e0" role="img" aria-label="Social profile"></div>
  <div class="social" style="left:724px;background:#2a7bb6" role="img" aria-label="Social profile"></div>
  <div class="social" style="left:759px;background:#d9483b" role="img" aria-label="Social profile"></div>
  <div class="footer-brand">Dornaby Accounting<br>and Bookkeeping</div>

  <div class="copyright-bar">Copyright © 2016&nbsp; Dornaby Accounting and Bookkeeping. All Right Reserved</div>
</footer>

</body>
</html>
```